Merrow Trade finance web design

We are a newly established business which provides invoice finance to Small Businesses in England and Wales.
Our approach is very much a funder where the small business owner can talk to the decision maker. We will guarantee on receipt of information, a decision within 24 hours.
We are not a bank so the look of the website need to be friendly but professional.
Have two types of people we are trying to attract to the website: 1) partners who are small business owners and 2) introducers who is accountants and commercial brokers who introduce us to the small businesses.
Currently no website, although domain has been reserved.
The design should be:
Professional
“Clean” Look
Designed to convey Trust and Authority.
Appeal to the small business owner.
Must incorporate:
Logo (attached)
Front page:Top tabs to other pages 1) About us 2) Services 3) Introducers 4) Contact us
Need picture and logo on page.
1) About us page- Room for talk about the company, the people and our critera.
2) Services page- We need for what invoice finance is, and 5 boxes for different services we will provide. (link on page to contact us)
3) Introducers page- We need a part for why become an introducer? Who we can help? Why we are different? (link on page to contact us)
4) Contact us page- Office address, email, tel and if possible a map and a contact me part which will email direct to us.
Text will be provided for the design, if we can see the setup of the website we will provide a part for each of the pages to support.
Styles we think convey the correct image:
www.dornelcapital.example
www.plivanlend.example
www.quorbacredit.example
Target Market(s)
Small business owners
Industry/Entity Type
Finance
Number of Pages Required
5+ page
Look and feel

```html
<!DOCTYPE html>
<html lang="en">
<head>
<meta charset="utf-8">
<title>Merrow Trade Finance Limited</title>
<link rel="stylesheet" href="https://fonts.googleapis.com/css2?family=Lato:wght@900&family=Open+Sans:wght@400;600;700&family=Raleway:wght@400;500;700&display=swap">
<style>
:root{
  --red:#d1343d;
  --red-dark:#b82a33;
  --ink:#111111;
  --text:#555555;
  --muted:#9a9a9a;
  --dark:#2d2d2d;
  --white:#ffffff;
  --line:#c9c9c9;
  --icon-grey:#bdbdbd;
}
*{box-sizing:border-box;margin:0;padding:0}
html,body{width:1200px;height:2853px;overflow:hidden}
body{position:relative;background:var(--white);font-family:"Open Sans",Arial,sans-serif;color:var(--text)}
.abs{position:absolute}
svg{display:block;flex:none}

/* top bar */
.topbar{left:0;top:0;width:1200px;height:51px;background:var(--red)}
.social{top:15px;left:98px;display:flex;gap:34px}
.social span{width:21px;height:21px;border-radius:50%;background:rgba(255,255,255,.85);display:block}
.contact-item{top:0;height:51px;display:flex;align-items:center;gap:10px;color:var(--white);font-size:18px;white-space:nowrap}

/* header */
.header{left:0;top:51px;width:1200px;height:124px;background:var(--white);border-bottom:4px solid var(--red)}
.brand{left:80px;top:80px;display:flex;align-items:center;gap:14px}
.brand-mark{width:34px;height:34px;border-radius:50%;background:var(--red)}
.brand-name{font-family:"Raleway",Arial,sans-serif;font-weight:700;font-size:27px;color:var(--red);line-height:1.1}
.nav{top:131px;font-size:18px;color:#444;letter-spacing:.3px;text-transform:uppercase;white-space:nowrap}
.nav.active{color:var(--red)}
.nav-pointer{left:474px;top:166px}

/* hero */
.hero{left:0;top:175px;width:1200px;height:573px;background:linear-gradient(100deg,#ffffff 0%,#f3f4f8 35%,#d7dbe8 65%,#b9bccb 100%)}
.hero-title{left:80px;top:300px;font-family:"Lato",Arial,sans-serif;font-weight:900;font-size:56px;line-height:73px;color:var(--ink);letter-spacing:-.3px}
.btn-dark{left:80px;top:535px;width:154px;height:46px;background:#2b2b2b;color:var(--white);font-size:20px;display:flex;align-items:center;justify-content:center;border-radius:3px}

/* section titles */
.section-title{left:0;width:1200px;text-align:center;font-family:"Raleway",Arial,sans-serif;font-weight:400;font-size:38px;color:var(--ink);text-transform:uppercase}
.section-title em{font-style:normal;color:var(--red)}
.section-title.light{color:var(--white)}

/* about */
.about-text{left:188px;top:864px;width:824px;text-align:center;font-size:15px;line-height:24px;color:var(--text)}
.btn-red{background:var(--red);color:var(--white);font-size:20px;display:flex;align-items:center;justify-content:center;border-radius:3px}
.about-btn{left:521px;top:978px;width:156px;height:45px}

/* services */
.services{left:0;top:1077px;width:1200px;height:468px;background:linear-gradient(90deg,#2a2a2a,#3b3b3b 50%,#262626)}
.card{top:1227px;width:325px;height:251px;background:var(--white);padding:34px 24px 0 22px}
.card.featured{background:rgba(185,40,48,.82)}
.card-head{display:flex;align-items:center;gap:22px;font-family:"Raleway",Arial,sans-serif;font-size:24px;color:var(--red)}
.card.featured .card-head{color:var(--white)}
.card p{margin-top:18px;padding-left:10px;font-size:15px;line-height:25px;color:#a5a5a5}
.card.featured p{color:#f3d3d5}
.card-link{position:absolute;left:22px;bottom:16px;display:flex;align-items:center;gap:10px;font-size:20px;color:var(--red)}
.card.featured .card-link{color:var(--white)}

/* why us */
.tabs{top:1660px;left:78px;display:flex;align-items:center;font-size:18px;color:var(--ink)}
.tab-active{width:126px;height:42px;border:1px solid var(--red);color:var(--red);display:flex;align-items:center;justify-content:center}
.why-text{left:80px;top:1721px;width:610px;font-size:15px;line-height:24px;color:var(--text)}
.why-list{left:74px;top:1858px;list-style:none;font-size:15px;color:var(--text)}
.why-list li{display:flex;align-items:center;gap:14px;height:50px}
.why-visual{left:709px;top:1716px;width:466px;height:344px;background:linear-gradient(180deg,#1f1f1f 0%,#2a2a2a 82%,#cfcfcf 82%,#e6e6e6 100%);border-radius:8px}

/* contact */
.touch{left:0;top:2058px;width:1200px;height:635px;background:linear-gradient(135deg,#4a4a4a,#3b3b3b 50%,#454545)}
.map{left:78px;top:2185px;width:523px;height:459px;background:linear-gradient(135deg,#e8e4dc,#dcd7cb 60%,#cfd8e3)}
.form{left:601px;top:2185px;width:521px;height:459px;background:var(--white)}
.field{left:647px;width:466px;height:37px;border-bottom:1px solid var(--line);display:flex;align-items:center;gap:14px;font-size:14px;color:#b5b5b5}
.field.message{height:95px;align-items:flex-start}
.submit{left:647px;top:2562px;width:156px;height:46px;background:#2b2b2b;color:var(--white);font-size:20px;display:flex;align-items:center;justify-content:center;border-radius:3px}

/* footer */
.footer-item{top:2704px;display:flex;align-items:center;gap:16px;font-size:14px;line-height:21px;color:#666;white-space:nowrap}
.bottombar{left:0;top:2800px;width:1200px;height:53px;background:var(--red);color:var(--white);font-size:15px;display:flex;align-items:center;justify-content:center}
.bottombar b{font-weight:700;margin:0 5px}
</style>
</head>
<body>

<!-- top bar -->
<div class="abs topbar"></div>
<div class="abs social" aria-label="Social links"><span></span><span></span><span></span></div>
<div class="abs contact-item" style="left:668px">
  <svg width="18" height="18" viewBox="0 0 24 24"><path fill="#fff" d="M6.6 10.8a15.1 15.1 0 0 0 6.6 6.6l2.2-2.2c.3-.3.7-.4 1-.2 1.1.4 2.3.6 3.6.6.6 0 1 .4 1 1V20c0 .6-.4 1-1 1A17 17 0 0 1 3 4c0-.6.4-1 1-1h3.5c.6 0 1 .4 1 1 0 1.3.2 2.5.6 3.6.1.3 0 .7-.2 1z"/></svg>
  020 7946 0321
</div>
<div class="abs contact-item" style="left:850px">
  <svg width="20" height="15" viewBox="0 0 20 15"><rect x="1" y="1" width="18" height="13" fill="none" stroke="#fff" stroke-width="1.6"/><path d="M1 1l9 7 9-7" fill="none" stroke="#fff" stroke-width="1.6"/></svg>
  merrowtrade@finance.example
</div>

<!-- header -->
<div class="abs header"></div>
<div class="abs brand"><span class="brand-mark"></span><span class="brand-name">Merrow Trade<br>Finance Limited</span></div>
<div class="abs nav active" style="left:458px">Home</div>
<div class="abs nav" style="left:576px">About</div>
<div class="abs nav" style="left:702px">Services</div>
<div class="abs nav" style="left:846px">Introducers</div>
<div class="abs nav" style="left:1035px">Contact</div>
<svg class="abs nav-pointer" width="18" height="10" viewBox="0 0 18 10"><path d="M0 0h18L9 10z" fill="#d1343d"/></svg>

<!-- hero -->
<div class="abs hero" role="img" aria-label="Photo of financial charts, banknotes and a calculator on a desk"></div>
<h1 class="abs hero-title">LOREM IPSUM IS SIMPLY<br>DUMMY TEXT OF THE<br>PRINTING.</h1>
<div class="abs btn-dark">GET A QUOTE</div>

<!-- about -->
<h2 class="abs section-title" style="top:798px">About <em>Us</em></h2>
<p class="abs about-text">Lorem Ipsum is simply dummy text of the printing and typesetting industry. Lorem Ipsum has been the industry's standard dummy text ever since the 1500s, when an unknown printer took a galley of type and scrambled it to make a type specimen book.It has survived not only five centuries, but also the leap into electronic typesetting, remaining essentially unchanged.</p>
<div class="abs btn-red about-btn">READ MORE</div>

<!-- services -->
<div class="abs services" role="img" aria-label="Dark photo of a business person at work"></div>
<h2 class="abs section-title light" style="top:1125px">Our <em>Services</em></h2>
<svg class="abs" style="left:30px;top:1316px" width="16" height="54" viewBox="0 0 16 54"><path d="M14 2L2 27l12 25" fill="none" stroke="#bbb" stroke-width="2"/></svg>
<svg class="abs" style="left:1154px;top:1316px" width="16" height="54" viewBox="0 0 16 54"><path d="M2 2l12 25-12 25" fill="none" stroke="#bbb" stroke-width="2"/></svg>

<div class="abs card featured" style="left:78px">
  <div class="card-head">
    <svg width="48" height="40" viewBox="0 0 48 40"><circle cx="16" cy="24" r="9" fill="none" stroke="#fff" stroke-width="5" stroke-dasharray="4 3"/><circle cx="16" cy="24" r="4" fill="none" stroke="#fff" stroke-width="2"/><circle cx="36" cy="11" r="7" fill="none" stroke="#fff" stroke-width="4" stroke-dasharray="3 3"/><circle cx="36" cy="11" r="3" fill="none" stroke="#fff" stroke-width="2"/></svg>
    Lorem Ipsum
  </div>
  <p>Lorem Ipsum is simply dummy text of the printing and typesetting industry. Lorem Ipsum has been the industry's standard dummy text</p>
  <div class="card-link">READ MORE <svg width="20" height="14" viewBox="0 0 20 14"><path d="M0 7h18M12 1l6 6-6 6" fill="none" stroke="currentColor" stroke-width="2"/></svg></div>
</div>
<div class="abs card" style="left:437px">
  <div class="card-head">
    <svg width="46" height="40" viewBox="0 0 46 40"><rect x="4" y="28" width="6" height="10" fill="#d1343d"/><rect x="14" y="22" width="6" height="16" fill="#d1343d"/><rect x="24" y="16" width="6" height="22" fill="#d1343d"/><rect x="34" y="10" width="6" height="28" fill="#d1343d"/><path d="M3 20L16 9l8 6L40 2" fill="none" stroke="#d1343d" stroke-width="2.5"/><path d="M34 2h7v7" fill="none" stroke="#d1343d" stroke-width="2.5"/></svg>
    Lorem Ipsum
  </div>
  <p>Lorem Ipsum is simply dummy text of the printing and typesetting industry. Lorem Ipsum has been the industry's standard dummy text</p>
  <div class="card-link">READ MORE <svg width="20" height="14" viewBox="0 0 20 14"><path d="M0 7h18M12 1l6 6-6 6" fill="none" stroke="#333" stroke-width="2"/></svg></div>
</div>
<div class="abs card" style="left:797px">
  <div class="card-head">
    <svg width="46" height="40" viewBox="0 0 46 40"><circle cx="27" cy="11" r="9" fill="none" stroke="#d1343d" stroke-width="2.5"/><text x="27" y="16" text-anchor="middle" font-size="13" font-family="Arial" fill="#d1343d" font-weight="700">$</text><path d="M2 28l8-4h10l6 3h12c3 0 3 4 0 4H24" fill="none" stroke="#d1343d" stroke-width="3"/><path d="M2 36l10-2 16 2 14-8" fill="none" stroke="#d1343d" stroke-width="3"/></svg>
    Lorem Ipsum
  </div>
  <p>Lorem Ipsum is simply dummy text of the printing and typesetting industry. Lorem Ipsum has been the industry's standard dummy text</p>
  <div class="card-link">READ MORE <svg width="20" height="14" viewBox="0 0 20 14"><path d="M0 7h18M12 1l6 6-6 6" fill="none" stroke="#333" stroke-width="2"/></svg></div>
</div>

<!-- why us -->
<h2 class="abs section-title" style="top:1593px">Why <em>Us Only?</em></h2>
<div class="abs tabs">
  <span class="tab-active">QUALITY</span>
  <span style="margin-left:64px">SERVICES</span>
  <span style="margin-left:56px">/</span>
  <span style="margin-left:50px">SUCESS</span>
</div>
<p class="abs why-text">Lorem Ipsum is simply dummy text of the printing and typesetting industry. Lorem Ipsum has been the industry's standard dummy text ever since the 1500s, when an unknown printer took a galley of type and scrambled it to make a type specimen book.It has survived not only five centuries, but also the leap into electronic typesetting, remaining essentially unchanged.</p>
<ul class="abs why-list">
  <li><svg width="10" height="16" viewBox="0 0 10 16"><path d="M0 0l10 8-10 8z" fill="#333"/></svg>Lorem Ipsum is simply dummy text of the printing.</li>
  <li><svg width="10" height="16" viewBox="0 0 10 16"><path d="M0 0l10 8-10 8z" fill="#333"/></svg>Lorem Ipsum has been the industry's standard dummy text</li>
  <li><svg width="10" height="16" viewBox="0 0 10 16"><path d="M0 0l10 8-10 8z" fill="#333"/></svg>Lorem Ipsum is simply dummy text of the printing.</li>
</ul>
<div class="abs why-visual" role="img" aria-label="Desktop monitor showing the company name"></div>

<!-- get in touch -->
<div class="abs touch" role="img" aria-label="Faded street map background"></div>
<h2 class="abs section-title light" style="top:2093px">Get <em>In Touch</em></h2>
<div class="abs map" role="img" aria-label="Street map of the office location"></div>
<div class="abs form"></div>
<div class="abs field" style="top:2207px"><svg width="16" height="16" viewBox="0 0 16 16"><circle cx="8" cy="5" r="3.5" fill="none" stroke="#b5b5b5"/><path d="M1.5 15c0-4 3-6 6.5-6s6.5 2 6.5 6" fill="none" stroke="#b5b5b5"/></svg>Name</div>
<div class="abs field" style="top:2281px"><svg width="16" height="16" viewBox="0 0 24 24"><path d="M6.6 10.8a15.1 15.1 0 0 0 6.6 6.6l2.2-2.2 4.6 1.5V20A17 17 0 0 1 3 4h4l1.6 4.6z" fill="none" stroke="#b5b5b5" stroke-width="1.8"/></svg>Contact No</div>
<div class="abs field" style="top:2349px"><svg width="17" height="13" viewBox="0 0 17 13"><rect x=".5" y=".5" width="16" height="12" fill="none" stroke="#b5b5b5"/><path d="M.5 .5l8 6 8-6" fill="none" stroke="#b5b5b5"/></svg>E mail Id</div>
<div class="abs field message" style="top:2428px"><svg width="16" height="16" viewBox="0 0 16 16"><rect x=".5" y="2.5" width="12" height="12" fill="none" stroke="#b5b5b5"/><path d="M6 10l1-3 7-7 2 2-7 7z" fill="none" stroke="#b5b5b5"/></svg>Message</div>
<div class="abs submit">SUBMIT</div>

<!-- footer -->
<div class="abs footer-item" style="left:76px">
  <svg width="26" height="40" viewBox="0 0 26 40"><path d="M13 0C6 0 0 5.5 0 12.5 0 22 13 40 13 40s13-18 13-27.5C26 5.5 20 0 13 0z" fill="#bdbdbd"/><circle cx="13" cy="12.5" r="5" fill="#fff"/></svg>
  <span>123,Lorem Ipsum is simply<br>dummy text of the printing.</span>
</div>
<div class="abs footer-item" style="left:527px;top:2719px">
  <svg width="40" height="40" viewBox="0 0 24 24"><path d="M6.6 10.8a15.1 15.1 0 0 0 6.6 6.6l2.2-2.2c.3-.3.7-.4 1-.2 1.1.4 2.3.6 3.6.6.6 0 1 .4 1 1V20c0 .6-.4 1-1 1A17 17 0 0 1 3 4c0-.6.4-1 1-1h3.5c.6 0 1 .4 1 1 0 1.3.2 2.5.6 3.6.1.3 0 .7-.2 1z" fill="#bdbdbd"/></svg>
  <span>020 7946 0321</span>
</div>
<div class="abs footer-item" style="left:850px;top:2722px">
  <svg width="42" height="30" viewBox="0 0 42 30"><rect width="42" height="30" rx="2" fill="#bdbdbd"/><path d="M2 3l19 14L40 3" fill="none" stroke="#fff" stroke-width="2.5"/></svg>
  <span>merrowtrade@finance.example</span>
</div>
<div class="abs bottombar">© <b>Merrow Trade Finance Limited</b> - 2016 All Right Reserved</div>

</body>
</html>
```